Website redesign for job agency recruitment

Please refer to the attached document, “Tarvenly Work Website Brief,” for comprehensive details regarding the scope, objectives, and requirements of this website redesign project.

For imagery you can use images from this website https://www.pixelmarrowfoto.com or any other you regularly use.

Target Market(s)

Jobseekers and Companies looking for general labour

Industry/Entity Type

Services: Oil, Gas and Mining, Administrative, Construction and Trades, Warehouse and Logistics and, Manufacturing.

Number of Pages Required

5+ page

Font styles to use
Serif
Other font styles liked:
• Inter, Open-Sans or similar.

Requirements
Must have
• The requirements highlighted in the Word document attached. The final design needs to be provided in Figma including all viewports (Desktop, mobiel and tablet)
Should not have
• Website we like as a reference: www.brevicktalentco.com, www.qelvaworks.com, www.zunmarra.com, www.ferrowhires.com, www.9vtalentpool.com, www.hiringwithtrello.ca

```html
<!DOCTYPE html>
<html lang="en">
<head>
<meta charset="utf-8">
<title>Tarvenly Work Agency Ltd.</title>
<link href="https://fonts.googleapis.com/css2?family=Barlow+Semi+Condensed:wght@500;600;700&family=Inter:wght@400;500;600&display=swap" rel="stylesheet">
<style>
:root{
  --navy:#1b3c9a;
  --navy-deep:#13286e;
  --yellow:#f4b605;
  --ink:#1b1b1f;
  --body:#4a4a52;
  --muted:#6b6e78;
  --cream:#fdfbf1;
  --grey-bg:#f2f3f5;
  --footer:#151b2d;
  --white:#ffffff;
}
*{margin:0;padding:0;box-sizing:border-box}
html,body{width:1200px;height:3693px;overflow:hidden}
body{position:relative;font-family:"Inter",sans-serif;color:var(--ink);background:var(--cream)}
.abs{position:absolute}
.head{font-family:"Barlow Semi Condensed",sans-serif;font-weight:600}
.hl{background:var(--yellow);color:var(--white);padding:0 6px}
.btn{position:absolute;display:flex;align-items:center;justify-content:center;font-size:14px;font-weight:600;color:var(--white);border-radius:3px;text-transform:uppercase}
.btn-yellow{background:var(--yellow)}
.btn-navy{background:var(--navy)}

/* header */
.site-header{top:0;left:0;width:1200px;height:125px;background:var(--cream)}
.brand{left:133px;top:22px;display:flex;align-items:center;gap:10px;font-family:"Barlow Semi Condensed",sans-serif;font-weight:700;font-size:22px;color:var(--navy)}
.brand-dot{width:40px;height:40px;border-radius:50%;background:var(--navy)}
.brand small{display:block}
.nav{top:86px;left:0;width:1200px;height:20px;font-size:14px;font-weight:500}
.nav a{position:absolute;color:var(--ink);text-decoration:none}
.nav a.active{color:var(--navy)}

/* hero */
.hero{top:125px;left:0;width:1200px;height:596px;background:linear-gradient(180deg,#2b2a2e 0%,#8a5418 35%,#e69a2a 48%,#6a3c14 62%,#1c1a1e 100%)}
.hero-shade{inset:0;background:linear-gradient(90deg,rgba(10,10,15,.55),rgba(10,10,15,.1))}
.hero h1{left:132px;top:158px;font-size:48px;line-height:56px;color:var(--white);font-weight:700}
.hero p{left:134px;top:280px;width:560px;font-size:17px;line-height:27px;color:var(--white)}
.dot{width:9px;height:9px;border-radius:50%;background:#9b9b9b;left:50px}
.dot.on{background:var(--yellow);box-shadow:0 0 0 4px rgba(244,182,5,.35)}

/* sectors */
.sectors{top:721px;left:0;width:1200px;height:852px;background:var(--grey-bg)}
.sec-title{top:44px;left:0;width:1200px;text-align:center;font-size:30px}
.sec-intro{top:98px;left:250px;width:700px;text-align:center;font-size:14px;line-height:23px;color:var(--body)}
.row{left:132px;width:935px;height:77px;background:var(--white);border-radius:6px;display:flex;align-items:center}
.row svg{margin-left:28px;width:46px;height:46px}
.row span{margin-left:24px;font-family:"Barlow Semi Condensed",sans-serif;font-weight:600;font-size:19px;text-transform:uppercase}
.row .arrow{position:absolute;right:30px;color:#c8c8cc;font-size:18px}
.row-open{top:278px;left:132px;width:935px;height:228px;border-radius:6px;overflow:hidden;background:linear-gradient(110deg,#24262c 0%,#3a3c44 45%,#7d6c62 75%,#c08450 100%)}
.row-open .fade{inset:0;background:linear-gradient(90deg,rgba(20,20,24,.9) 0%,rgba(20,20,24,.5) 48%,rgba(20,20,24,0) 70%)}
.row-open h3{left:100px;top:50px;font-size:20px;color:var(--white);text-decoration:underline;text-decoration-color:var(--yellow)}
.row-open p{left:30px;top:96px;width:420px;font-size:13px;line-height:23px;color:var(--white)}
.go{right:42px;top:95px;width:52px;height:52px;border-radius:50%;background:var(--yellow);color:var(--white);display:flex;align-items:center;justify-content:center;font-size:22px}

/* about */
.about{top:1573px;left:0;width:1200px;height:575px;background:var(--cream)}
.about-frame{left:162px;top:102px;width:397px;height:418px;border:1px solid #e8cf80}
.photo-team{left:130px;top:73px;width:415px;height:434px;background:linear-gradient(160deg,#b8c2cc,#8a8f94 50%,#c9a98a)}
.photo-deal{left:413px;top:331px;width:173px;height:178px;background:linear-gradient(160deg,#2c3038,#6b6e72);border:4px solid var(--cream)}
.about h2{left:652px;top:80px;font-size:31px;line-height:40px}
.about p{left:653px;width:415px;font-size:13.5px;line-height:22.5px;color:var(--body)}

/* results */
.results{top:2148px;left:0;width:1200px;height:547px;background:linear-gradient(180deg,#1b3c9a,#18378f)}
.results h2{top:62px;left:0;width:1200px;text-align:center;font-size:30px;color:var(--white);text-transform:uppercase}
.results .lead{top:127px;left:300px;width:600px;text-align:center;font-size:14px;line-height:23px;color:#e6eaf7}
.card{top:225px;width:292px;height:262px;background:var(--white);border-radius:3px;text-align:center}
.card svg{position:absolute;left:106px;top:30px;width:80px;height:80px}
.card h4{position:absolute;top:138px;left:0;width:100%;font-family:"Barlow Semi Condensed",sans-serif;font-weight:600;font-size:19px;color:var(--navy);text-transform:uppercase}
.card p{position:absolute;top:174px;left:34px;width:224px;font-size:12.5px;line-height:19px;color:var(--muted)}

/* insights */
.insights{top:2695px;left:0;width:1200px;height:578px;background:var(--cream)}
.insights h2{top:48px;left:0;width:1200px;text-align:center;font-size:31px}
.img-refinery{left:132px;top:122px;width:456px;height:294px;background:linear-gradient(180deg,#173f8a,#1f3a6a 55%,#d07a22 80%,#2a1a10)}
.img-warehouse{left:611px;top:122px;width:185px;height:197px;background:linear-gradient(180deg,#5b6a78,#a9b2b8 60%,#6a7078)}
.img-crew{left:611px;top:342px;width:185px;height:177px;background:linear-gradient(160deg,#8a5a34,#c89a58 45%,#4a3a2e)}
.post-title{font-family:"Barlow Semi Condensed",sans-serif;font-weight:600;color:var(--ink)}
.post-text{font-size:12.5px;line-height:19px;color:var(--body)}
.more{font-size:12.5px;color:var(--yellow);text-decoration:underline}

/* footer */
.site-footer{top:3273px;left:0;width:1200px;height:420px;background:var(--footer);color:#c9ccd6}
.vline{top:0;width:1px;height:350px;background:#2c3347}
.f-brand{left:133px;top:80px;display:flex;align-items:center;gap:10px;font-family:"Barlow Semi Condensed",sans-serif;font-weight:700;font-size:24px;color:var(--navy)}
.f-brand i{display:block;width:44px;height:44px;border-radius:50%;background:var(--navy)}
.social{width:28px;height:28px;border-radius:50%;border:1px solid #c9ccd6;top:211px}
.f-head{top:73px;font-family:"Barlow Semi Condensed",sans-serif;font-weight:600;font-size:17px;color:var(--yellow)}
.f-list{top:126px;list-style:none;font-size:13px;line-height:32px}
.addr{left:888px;font-size:13px;line-height:23px}
.copy-line{left:0;top:350px;width:1200px;height:1px;background:#2c3347}
.copy{top:374px;left:0;width:1200px;text-align:center;font-size:12.5px}
</style>
</head>
<body>

<header class="site-header abs">
  <div class="brand abs"><span class="brand-dot"></span><span>Tarvenly Work<small>Agency Ltd.</small></span></div>
  <div class="btn btn-yellow" style="left:650px;top:20px;width:217px;height:40px;font-size:12.5px;gap:8px">
    <svg width="14" height="14" viewBox="0 0 24 24" fill="none" stroke="#fff" stroke-width="2"><path d="M5 3h4l2 5-3 2a12 12 0 0 0 6 6l2-3 5 2v4a2 2 0 0 1-2 2A18 18 0 0 1 3 5a2 2 0 0 1 2-2z"/></svg>
    Toll Free: 1-888-555-0142</div>
  <div class="btn btn-yellow" style="left:896px;top:20px;width:172px;height:40px;font-size:12.5px">Client Registration</div>
  <nav class="nav abs">
    <a class="active" style="left:439px">Home</a>
    <a style="left:528px">Services</a>
    <a style="left:635px">Candidates</a>
    <a style="left:760px">Employers</a>
    <a style="left:880px">About Us</a>
    <a style="left:992px">Contact Us</a>
  </nav>
</header>

<section class="hero abs" role="img" aria-label="City skyline at sunset reflected on glass floor">
  <div class="hero-shade abs"></div>
  <h1 class="abs head">The Right People to<br>Power Your Business.</h1>
  <p class="abs">Modern recruitment solutions designed to enhance brand credibility and improve engagement for candidates and employers.</p>
  <div class="btn btn-navy" style="left:132px;top:358px;width:185px;height:48px">For Candidates</div>
  <div class="btn btn-yellow" style="left:335px;top:358px;width:187px;height:48px">For Candidates</div>
  <span class="dot abs" style="top:215px"></span>
  <span class="dot on abs" style="top:247px"></span>
  <span class="dot abs" style="top:279px"></span>
</section>

<section class="sectors abs">
  <h2 class="sec-title abs head">Sectors We <span class="hl">Serve</span></h2>
  <p class="sec-intro abs">At Tarvenly Work Agency Ltd., we specialize in connecting high-caliber talent with industry-leading organizations. Our deep-rooted expertise across five core sectors allows us to provide tailored recruitment solutions that drive operational success and long-term growth</p>

  <div class="row abs" style="top:189px">
    <svg viewBox="0 0 48 48" fill="none" stroke="#222" stroke-width="1.6"><path d="M6 40h36M10 40l4-12h20l4 12M18 28V12h12v16M22 12V6M14 20h20"/></svg>
    <span>Oil, Gas &amp; Mining</span><b class="arrow">→</b></div>

  <div class="row-open abs" role="img" aria-label="High-rise buildings under construction with cranes at dusk">
    <div class="fade abs"></div>
    <svg class="abs" style="left:30px;top:36px" width="44" height="44" viewBox="0 0 48 48" fill="none" stroke="#f4b605" stroke-width="1.8"><path d="M12 22a12 12 0 0 1 24 0M9 22h30M16 44v-8a8 8 0 0 1 16 0v8"/><circle cx="24" cy="28" r="4"/></svg>
    <h3 class="abs head">CONSTRUCTION &amp; TRADES</h3>
    <p class="abs">Tarvenly Work Agency is a premiere construction staffing agency that can provide you with reliable, experienced, and skilled tradespeople for projects all over Canada. We provide labour for temp, temp-to-hire, and permanent positions.</p>
    <div class="go abs">→</div>
  </div>

  <div class="row abs" style="top:526px">
    <svg viewBox="0 0 48 48" fill="none" stroke="#222" stroke-width="1.6"><rect x="16" y="6" width="16" height="14"/><rect x="6" y="22" width="16" height="14"/><rect x="26" y="22" width="16" height="14"/><path d="M4 40h40"/></svg>
    <span>Warehouse &amp; Logistics</span><b class="arrow">→</b></div>
  <div class="row abs" style="top:619px">
    <svg viewBox="0 0 48 48" fill="none" stroke="#222" stroke-width="1.6"><rect x="6" y="14" width="36" height="24" rx="2"/><path d="M18 14V9h12v5M6 24h36"/></svg>
    <span>Administrative</span><b class="arrow">→</b></div>
  <div class="row abs" style="top:710px">
    <svg viewBox="0 0 48 48" fill="none" stroke="#222" stroke-width="1.6"><path d="M6 42V20l10 6v-6l10 6v-6l10 6V8h6v34z"/><path d="M12 34h4M22 34h4M32 34h4"/></svg>
    <span>Manufacturing</span><b class="arrow">→</b></div>
</section>

<section class="about abs">
  <div class="about-frame abs"></div>
  <div class="photo-team abs" role="img" aria-label="Business team meeting around an office table"></div>
  <div class="photo-deal abs" role="img" aria-label="Two businessmen shaking hands"></div>
  <h2 class="abs head">Strengthening Your Business<br>with <span class="hl">Precision Staffing</span></h2>
  <p class="abs" style="top:170px">Tarvenly Work Agency Ltd. provides a complete range of recruitment services designed to keep pace with the rapidly changing demands of modern business. We are a Canada-wide team of search specialists and business consultants who thrive on delivering customized solutions that evolve with your market.</p>
  <p class="abs" style="top:328px">With specialist divisions immersed in the heartbeat of five core industries, we are the 'go-to' partners who successfully manage thousands of relationships every day. Our goal is simple: to provide results that are on-time, on-budget, and powered by the right people."</p>
  <div class="btn btn-yellow" style="left:650px;top:457px;width:152px;height:42px;font-size:13px">About Agency</div>
</section>

<section class="results abs">
  <h2 class="abs head">Your Vision. Our Expertise. <span class="hl">Real Results</span></h2>
  <p class="lead abs">At Tarvenly Work Agency Ltd., we strive to have a meaningful impact on every business we power. For years, we have helped clients and candidates find innovative staffing solutions through strategic partnership and knowledge sharing</p>

  <div class="card abs" style="left:135px">
    <svg viewBox="0 0 80 80" fill="none" stroke="#f4b605" stroke-width="2"><path d="M20 18l3 6 6 1-4 4 1 6-6-3-6 3 1-6-4-4 6-1zM40 10l3 6 6 1-4 4 1 6-6-3-6 3 1-6-4-4 6-1zM60 18l3 6 6 1-4 4 1 6-6-3-6 3 1-6-4-4 6-1z"/><circle cx="40" cy="52" r="6"/><circle cx="24" cy="56" r="5"/><circle cx="56" cy="56" r="5"/><path d="M28 74a12 12 0 0 1 24 0M14 74a10 10 0 0 1 18-4M48 70a10 10 0 0 1 18 4"/></svg>
    <h4>98 % Client Satisfaction</h4>
    <p>Our clients report that TWA provides the talent and data needed to complete their strategic priorities</p>
  </div>
  <div class="card abs" style="left:455px">
    <svg viewBox="0 0 80 80" fill="none" stroke="#f4b605" stroke-width="2"><circle cx="40" cy="32" r="20"/><circle cx="40" cy="32" r="13"/><path d="M40 24l3 6 6 1-4 4 1 6-6-3-6 3 1-6-4-4 6-1zM26 46l-10 20 10-2 5 8 7-20M54 46l10 20-10-2-5 8-7-20"/></svg>
    <h4>#1 Specialized Staffing</h4>
    <p>Recognized as a leading brand in specialized recruitment for Western Canada's core industrial sectors</p>
  </div>
  <div class="card abs" style="left:776px">
    <svg viewBox="0 0 80 80" fill="none" stroke="#f4b605" stroke-width="2"><path d="M12 68a28 28 0 1 1 56 0z"/><path d="M20 68a20 20 0 1 1 40 0M40 68l10-18"/><path d="M30 14l2 4 4 1-3 3 1 4-4-2-4 2 1-4-3-3 4-1zM50 14l2 4 4 1-3 3 1 4-4-2-4 2 1-4-3-3 4-1z"/></svg>
    <h4>10+ Years of Expertise</h4>
    <p>Providing a complete range of recruitment services immersed in the heartbeat of Canada's core industries</p>
  </div>
</section>

<section class="insights abs">
  <h2 class="abs head">Latest Market <span class="hl">Insights</span></h2>
  <div class="img-refinery abs" role="img" aria-label="Refinery towers with flare at night"></div>
  <h3 class="post-title abs" style="left:134px;top:441px;width:440px;font-size:21px;line-height:25px">The 2026 Outlook: Powering Western Canada's Energy Evolution</h3>
  <p class="post-text abs" style="left:136px;top:493px;width:430px">We analyze the critical need for specialized talent in the heartbeat of the energy sector as the industrial landscape shifts.</p>

  <div class="img-warehouse abs" role="img" aria-label="Empty warehouse interior with forklifts and racks"></div>
  <h3 class="post-title abs" style="left:820px;top:132px;width:240px;font-size:16px;line-height:24px">Beyond the Warehouse: Optimizing Supply Human Capita</h3>
  <p class="post-text abs" style="left:822px;top:193px;width:230px">We analyze the critical need for specialized talent in the heartbeat of the energy sector as the industrial landscape shifts.</p>
  <span class="more abs" style="left:823px;top:290px">Read More</span>

  <div class="img-crew abs" role="img" aria-label="Construction crew in hard hats on a site"></div>
  <h3 class="post-title abs" style="left:820px;top:345px;width:240px;font-size:16px;line-height:24px">Bridging the Gap in Specialized Construction Trade</h3>
  <p class="post-text abs" style="left:822px;top:405px;width:230px">We explore specialized recruitment models that help our partners deliver projects on-time and on-budget across Canada.</p>
  <span class="more abs" style="left:824px;top:485px">Read More</span>
</section>

<footer class="site-footer abs">
  <span class="vline abs" style="left:357px"></span>
  <span class="vline abs" style="left:565px"></span>
  <span class="vline abs" style="left:796px"></span>
  <div class="f-brand abs"><i></i>Tarvenly Work</div>
  <span class="social abs" style="left:168px"></span>
  <span class="social abs" style="left:205px"></span>

  <h5 class="f-head abs" style="left:411px">Quick Links</h5>
  <ul class="f-list abs" style="left:413px"><li>Home</li><li>Services</li><li>Candidates</li><li>Employers</li><li>About us</li><li>Contact us</li></ul>

  <h5 class="f-head abs" style="left:614px">Our Services</h5>
  <ul class="f-list abs" style="left:615px"><li>Oil, Gas and Mining</li><li>Administrative</li><li>Construction and Trades</li><li>Warehouse and Logistics</li><li>Manufacturing.</li></ul>

  <h5 class="f-head abs" style="left:853px">Our Address</h5>
  <svg class="abs" style="left:848px;top:126px" width="22" height="22" viewBox="0 0 24 24" fill="none" stroke="#c9ccd6" stroke-width="1.5"><path d="M4 22V6h10v16M14 10h6v12M2 22h20M7 10h2M7 14h2M7 18h2"/></svg>
  <p class="addr abs" style="top:124px">418 Marrow Ave SW Calgary,<br>AB, T2P 4K9</p>
  <svg class="abs" style="left:850px;top:201px" width="18" height="18" viewBox="0 0 24 24" fill="none" stroke="#c9ccd6" stroke-width="1.6"><path d="M5 3h4l2 5-3 2a12 12 0 0 0 6 6l2-3 5 2v4a2 2 0 0 1-2 2A18 18 0 0 1 3 5a2 2 0 0 1 2-2z"/></svg>
  <p class="addr abs" style="top:199px">Toll-Free: 1-888-555-0142</p>
  <svg class="abs" style="left:850px;top:241px" width="18" height="18" viewBox="0 0 24 24" fill="none" stroke="#c9ccd6" stroke-width="1.6"><path d="M5 3h4l2 5-3 2a12 12 0 0 0 6 6l2-3 5 2v4a2 2 0 0 1-2 2A18 18 0 0 1 3 5a2 2 0 0 1 2-2z"/></svg>
  <p class="addr abs" style="top:239px">403-555-0178</p>

  <span class="copy-line abs"></span>
  <p class="copy abs">© Tarvenly Work Agency Ltd. | All rights reserved 2026</p>
</footer>

</body>
</html>
```